Web Design for a Biotech Consulting Firm

We need a web site design for a new business based in Philadelphia called Verantel Dx. This is a consulting firm that will serve medical diagnostics industry, which is part of the life science/healthcare industry focusing on developing and marketing products that help in early detection, monitoring or management of diseases. Our consulting firm will help medical diagnostic companies to overcome key challenges in designing, evaluating and marketing new products.Our company name is Verantel Dx. Verantel is Latin word for "something" Dx represents diagnostics. The idea behind the name is that we help companies to transform the original, early product ideas ("nothing") into "something"; which is a product with full clinical utility that will help to improve health and well-being.The web site should use the visual feel of the logo (attached), be modern, simple and clean looking and represent creativity, innovation, scientific thinking and progress.
Updates

Wix Design is acceptable

Industry/Entity Type

Biotechnology

Coding

Coded - Design and coding required

Number of Pages Required

1 page

Font styles to use
Sans Serif

Requirements
Must have
• simple, clean look couple of pages
Should not have
• a lot of pages

```html
<!DOCTYPE html>
<html lang="en">
<head>
<meta charset="utf-8">
<title>Verantel Dx — Biotech Consulting Firm</title>
<link href="https://fonts.googleapis.com/css2?family=Outfit:wght@300;400;500;600;700&display=swap" rel="stylesheet">
<style>
:root{
  --blue:#1f7fec;
  --blue-dark:#0d4f9e;
  --ink:#222429;
  --muted:#5a5d63;
  --line:#d7dbe2;
  --light:#f4f5f7;
  --footer:#3b3e44;
  --footer-deep:#2f3237;
  --white:#ffffff;
}
*{box-sizing:border-box;margin:0;padding:0}
html,body{width:1200px;height:3143px;overflow:hidden}
body{font-family:"Outfit",sans-serif;color:var(--ink);background:var(--white);position:relative}
.abs{position:absolute}
.accent{color:var(--blue)}
.section-title{position:absolute;left:0;width:1200px;text-align:center;font-size:33px;font-weight:400}
.section-rule{position:absolute;left:578px;width:44px;height:2px;background:var(--blue)}

/* header */
.brand-name{position:absolute;white-space:nowrap;font-weight:400;color:var(--ink)}
.contact-chip{position:absolute;top:14px;display:flex;align-items:center;gap:10px;font-size:17px}
.chip-icon{width:29px;height:29px;border:2px solid var(--blue);display:flex;align-items:center;justify-content:center}
.nav{position:absolute;top:72px;left:522px;display:flex;font-size:14px}
.nav a{color:var(--ink);text-decoration:none;margin-right:60px}
.nav a.active{color:var(--blue)}

/* hero */
.hero{position:absolute;top:106px;left:0;width:1200px;height:494px;
  background:radial-gradient(circle at 65% 35%,#3c8fe0 0%,#1c5fb0 45%,#0b2f6a 100%)}
.hero-frame{position:absolute;left:283px;top:295px;width:634px;height:127px;border:2px solid rgba(255,255,255,.85);border-top:none}
.hero-frame-top{position:absolute;top:295px;width:30px;height:2px;background:rgba(255,255,255,.85)}
.hero-title{position:absolute;left:0;width:1200px;top:272px;text-align:center;color:#fff;font-size:43px;font-weight:700;line-height:50px}
.hero-sub{position:absolute;left:0;width:1200px;top:330px;text-align:center;color:#fff;font-size:16.5px;line-height:26px}
.btn{position:absolute;background:var(--blue);color:#fff;font-size:13.5px;display:flex;align-items:center;justify-content:center;gap:6px;border:1px solid #fff}
.dots{position:absolute;display:flex;gap:6px}
.dots i{display:block;width:8px;height:8px;border:1px solid #fff}
.dots i.on{background:#fff}
.dots.blue i{border-color:var(--blue)}
.dots.blue i.on{background:var(--blue)}

/* about */
.about-frame{position:absolute;left:141px;top:671px;width:437px;height:401px;border:2px solid var(--blue)}
.photo{position:absolute;left:162px;top:691px;width:438px;height:359px;
  background:linear-gradient(135deg,#a9c4dd 0%,#e7ecf1 45%,#6fa06b 75%,#dfe5ea 100%)}
.about-text{position:absolute;left:684px;width:376px}
.about-text p{font-size:12px;line-height:19px;color:var(--muted)}
.mv{position:absolute;left:684px;display:flex;gap:20px}
.mv-icon{width:53px;height:53px;border:1.5px solid var(--blue);display:flex;align-items:center;justify-content:center;flex:none}
.mv h4{font-size:15px;font-weight:500;margin-bottom:4px}
.mv p{font-size:12px;line-height:16px;color:var(--muted)}
.link-more{position:absolute;color:var(--blue);font-size:13.5px;display:flex;align-items:center;gap:6px}

/* services */
.services-band{position:absolute;top:1143px;left:0;width:1200px;height:305px;
  background:linear-gradient(120deg,#2b86ee 0%,#1f7fec 60%,#2a84ea 100%)}
.card{position:absolute;top:1326px;height:229px;background:#fff;border:1.5px solid var(--blue);text-align:center}
.card svg{position:absolute;top:28px;left:50%;transform:translateX(-50%)}
.card h3{position:absolute;top:110px;width:100%;font-size:17px;font-weight:500}
.card p{position:absolute;top:140px;left:18px;right:18px;font-size:12px;line-height:16px;color:var(--muted)}
.plus{position:absolute;bottom:-13px;left:50%;transform:translateX(-50%);width:25px;height:25px;border:1.5px solid var(--blue);background:#fff;color:var(--blue);font-size:19px;line-height:20px}
.plus.on{background:var(--blue);color:#fff}

/* why */
.why{position:absolute;top:1639px;left:0;width:1200px;height:503px;background:linear-gradient(180deg,#f2f4f7,#eceff3)}
.why-box{position:absolute;width:71px;height:71px;border:1.5px solid var(--blue);background:#fff;display:flex;align-items:center;justify-content:center}
.why-box.on{background:var(--blue)}
.why-label{position:absolute;font-size:15px}
.why-center{position:absolute;left:494px;top:1839px;width:211px;height:182px;background:#fff;box-shadow:0 4px 18px rgba(0,0,0,.06);display:flex;align-items:center;justify-content:center;font-size:28px;color:var(--ink)}

/* reviews */
.arrow-box{position:absolute;width:31px;height:31px;border:1.5px solid var(--blue);display:flex;align-items:center;justify-content:center}
.quote{position:absolute;left:312px;width:576px;top:2343px;text-align:center;font-size:14px;line-height:22.5px;font-style:italic;color:var(--muted)}

/* partners */
.partners{position:absolute;top:2540px;left:0;width:1200px;height:317px;background:var(--light)}
.tile{position:absolute;top:2689px;width:169px;height:98px;background:#fff;border:1px solid #e4e6ea;display:flex;align-items:center;justify-content:center}
.tile.lift{box-shadow:0 3px 10px rgba(0,0,0,.12)}

/* footer */
.footer{position:absolute;top:2857px;left:0;width:1200px;height:286px;background:linear-gradient(120deg,#44474d,#35383d)}
.copy{position:absolute;top:3098px;left:0;width:1200px;height:45px;background:var(--footer-deep);color:#d8d9dc;font-size:11px;text-align:center;line-height:45px}
.f-head{position:absolute;top:2905px;color:#fff;font-size:16px}
.f-head::after{content:"";position:absolute;left:0;top:27px;width:34px;height:2px;background:var(--blue)}
.f-list{position:absolute;top:2948px;list-style:none;color:#fff;font-size:11px}
.f-list li{height:25px;padding-left:10px;position:relative}
.f-list li::before{content:"";position:absolute;left:0;top:5px;width:4px;height:4px;border-radius:50%;background:#8a8d93}
.f-line{position:absolute;height:1px;background:#5b5e64}
.f-item{position:absolute;color:#fff;font-size:11px;line-height:14px;display:flex;gap:12px}
.f-input{position:absolute;left:593px;top:2990px;width:212px;height:31px;border:1px solid #75787e;color:#b9bbbf;font-size:11px;padding:9px 10px}
.social{position:absolute;top:3033px;width:31px;height:31px;border:1.5px solid #fff}
.social.on{background:var(--blue);border-color:var(--blue)}
</style>
</head>
<body>

<!-- header -->
<header>
  <div class="brand-name" style="left:141px;top:39px;font-size:21px">Verantel Dx</div>
  <div class="contact-chip" style="left:727px">
    <span class="chip-icon"><svg width="14" height="14" viewBox="0 0 24 24"><path d="M6.6 10.8a15 15 0 0 0 6.6 6.6l2.2-2.2c.3-.3.7-.4 1-.2 1.1.4 2.3.6 3.6.6.6 0 1 .4 1 1V20c0 .6-.4 1-1 1A17 17 0 0 1 3 4c0-.6.4-1 1-1h3.5c.6 0 1 .4 1 1 0 1.3.2 2.5.6 3.6.1.3 0 .7-.2 1z" fill="#1f7fec"/></svg></span>
    <span>123 456 7890</span>
  </div>
  <div class="contact-chip" style="left:896px;font-size:13.5px">
    <span class="chip-icon"><svg width="14" height="11" viewBox="0 0 14 11"><rect width="14" height="11" rx="1" fill="#1f7fec"/><path d="M1 1l6 5 6-5" stroke="#fff" fill="none" stroke-width="1.3"/></svg></span>
    <span>info@verantel-dx.com</span>
  </div>
  <nav class="nav">
    <a class="active" href="#">Home</a><a href="#">About Us</a><a href="#">Services</a><a href="#">Resources</a><a href="#" style="margin-right:0">Contact Us</a>
  </nav>
  <div class="abs" style="left:522px;top:104px;width:40px;height:2px;background:var(--blue)"></div>
</header>

<!-- hero -->
<section class="hero" role="img" aria-label="Blue-toned backdrop of a DNA double helix"></section>
<div class="hero-frame"></div>
<div class="hero-frame-top" style="left:283px"></div>
<div class="hero-frame-top" style="left:887px"></div>
<h1 class="hero-title">BIOTECH CONSULTING FIRM</h1>
<p class="hero-sub">We Serve Medical Diagnostics Industry, Which Is Part Of The<br>Life Science/healthcare Industry.</p>
<div class="btn" style="left:527px;top:401px;width:147px;height:40px">READ MORE <svg width="16" height="8" viewBox="0 0 16 8"><path d="M0 4h15M11 1l4 3-4 3" stroke="#fff" fill="none"/></svg></div>
<div class="dots" style="left:575px;top:557px"><i class="on"></i><i></i><i></i><i></i></div>

<!-- about -->
<div class="about-frame"></div>
<div class="photo" role="img" aria-label="Scientist in a lab coat placing a seedling into a petri dish with tweezers"></div>
<h2 class="abs" style="left:686px;top:683px;font-size:33px;font-weight:400">About <span class="accent">Us</span></h2>
<div class="abs" style="left:686px;top:730px;width:44px;height:2px;background:var(--blue)"></div>
<div class="about-text" style="top:750px">
  <h4 style="font-size:15px;font-weight:500;margin-bottom:7px">Duis autem vel eum iriure dolor in hendrerit.</h4>
  <p>Lorem ipsum dolor sit amet, consectetuer adipiscing elit, sedmk diam nonummy nibh euismod tincidunt ut laoreet dolore magna aliquam erat volutpat. Suscipit lobortis nisl ut aliquip ex eamo kl commodo consequat.</p>
</div>
<div class="mv" style="top:878px">
  <div class="mv-icon"><svg width="28" height="28" viewBox="0 0 28 28" fill="none" stroke="#555" stroke-width="1.4"><circle cx="13" cy="15" r="11"/><circle cx="13" cy="15" r="6.5"/><circle cx="13" cy="15" r="2"/><path d="M13 15L24 4M20 4h4v4"/></svg></div>
  <div><h4>Mission</h4><p>Accumsan et iusto odio dignissim qui blandit dollarl<br>praesent luptatum zzril delenit augue.</p></div>
</div>
<div class="mv" style="top:958px">
  <div class="mv-icon"><svg width="32" height="20" viewBox="0 0 32 20" fill="none" stroke="#555" stroke-width="1.4"><path d="M1 10C6 3 11 1 16 1s10 2 15 9c-5 7-10 9-15 9S6 17 1 10z"/><circle cx="16" cy="10" r="5"/><circle cx="16" cy="10" r="2"/></svg></div>
  <div><h4>Vision</h4><p>Accumsan et iusto odio dignissim qui blandit dollarl<br>praesent luptatum zzril delenit augue.</p></div>
</div>
<div class="link-more" style="left:684px;top:1039px">READ MORE <svg width="16" height="8" viewBox="0 0 16 8"><path d="M0 4h15M11 1l4 3-4 3" stroke="#1f7fec" fill="none"/></svg></div>

<!-- services -->
<section class="services-band" role="img" aria-label="Faint DNA helix texture over blue"></section>
<h2 class="section-title" style="top:1205px;color:#fff">Our Services</h2>
<p class="abs" style="left:0;width:1200px;top:1274px;text-align:center;color:#fff;font-size:14.5px;font-weight:500">Lorem ipsum dolor sit amet, consectetuer adipiscing elit, sedmk diam nonummy nibh euismod.</p>

<div class="card" style="left:141px;width:218px">
  <svg width="58" height="56" viewBox="0 0 58 56" fill="none" stroke="#1f7fec" stroke-width="1.5"><circle cx="18" cy="24" r="13"/><path d="M9 34L2 45"/><circle cx="38" cy="28" r="16"/><path d="M38 18v10l7 5M35 10h6M38 10v2"/></svg>
  <h3>Corporate Strategy</h3>
  <p>Lorem ipsum dolor sit amet, consectetuer adipiscing elit, sedmk diam nonummy.</p>
  <div class="plus on">+</div>
</div>
<div class="card" style="left:378px;width:214px">
  <svg width="58" height="58" viewBox="0 0 58 58" fill="none" stroke="#1f7fec" stroke-width="1.5"><path d="M8 30l21-10 21 10-21 10z"/><path d="M8 30v14l21 12 21-12V30M29 40v16"/><circle cx="29" cy="14" r="6"/><path d="M29 2v4M19 8l3 2M39 8l-3 2M27 20h4v4h-4z"/></svg>
  <h3>Product Development</h3>
  <p>Lorem ipsum dolor sit amet, consectetuer adipiscing elit, sedmk diam nonummy.</p>
  <div class="plus">+</div>
</div>
<div class="card" style="left:611px;width:214px">
  <svg width="60" height="60" viewBox="0 0 60 60" fill="none" stroke="#1f7fec" stroke-width="1.5"><path d="M8 2h32l10 10v46H8z"/><circle cx="25" cy="30" r="8"/><circle cx="25" cy="30" r="3"/><circle cx="40" cy="30" r="5"/><path d="M25 18v4M25 38v4M13 30h4M46 30h8M12 50h20"/></svg>
  <h3>Business Development</h3>
  <p>Lorem ipsum dolor sit amet, consectetuer adipiscing elit, sedmk diam nonummy.</p>
  <div class="plus">+</div>
</div>
<div class="card" style="left:844px;width:214px">
  <svg width="58" height="54" viewBox="0 0 58 54" fill="none" stroke="#1f7fec" stroke-width="1.5"><path d="M4 2h50l3 14H1z"/><path d="M6 16v36h46V16M12 52V30h12v22M30 28h16v14H30zM38 31v8M34 35h8"/></svg>
  <h3>Commercialization</h3>
  <p>Lorem ipsum dolor sit amet, consectetuer adipiscing elit, sedmk diam nonummy.</p>
  <div class="plus">+</div>
</div>

<!-- why choose -->
<section class="why" role="img" aria-label="Soft pale laboratory backdrop"></section>
<h2 class="section-title" style="top:1696px">Why Choose <span class="accent">Us?</span></h2>
<div class="section-rule" style="top:1745px"></div>
<svg class="abs" style="left:382px;top:1824px" width="436" height="212" fill="none" stroke="#c5cfdb" stroke-width="1">
  <path d="M0 1h56l55 50M0 107h112M0 213h56l55-50M436 1h-56l-55 50M436 107h-112M436 213h-56l-55-50"/>
</svg>
<div class="why-center">Verantel Dx</div>

<div class="why-label" style="right:902px;top:1813px">Years Of Experience</div>
<div class="why-box on" style="left:311px;top:1789px"><svg width="34" height="38" viewBox="0 0 34 38" fill="none" stroke="#fff" stroke-width="1.5"><circle cx="17" cy="15" r="13"/><circle cx="17" cy="15" r="8"/><path d="M13 15l3 3 5-6M9 26l-4 10 5-2 3 4 3-8M25 26l4 10-5-2-3 4-3-8"/></svg></div>
<div class="why-label" style="right:902px;top:1920px">Proffesional Team</div>
<div class="why-box" style="left:311px;top:1895px"><svg width="42" height="34" viewBox="0 0 42 34" fill="none" stroke="#555" stroke-width="1.4"><circle cx="21" cy="10" r="6"/><circle cx="8" cy="14" r="4.5"/><circle cx="34" cy="14" r="4.5"/><path d="M10 33c0-8 5-13 11-13s11 5 11 13M1 30c0-5 3-8 7-8M41 30c0-5-3-8-7-8"/></svg></div>
<div class="why-label" style="right:902px;top:2026px">Best Valuation</div>
<div class="why-box" style="left:311px;top:2001px"><svg width="40" height="40" viewBox="0 0 40 40" fill="none" stroke="#555" stroke-width="1.4"><path d="M12 4h16l6 8-14 14L6 12z"/><path d="M6 12h28M16 4l-2 8 6 14 6-14-2-8"/><path d="M4 26l16 8 16-8v8l-16 6-16-6z"/></svg></div>

<div class="why-box" style="left:818px;top:1789px"><svg width="36" height="40" viewBox="0 0 36 40" fill="none" stroke="#555" stroke-width="1.4"><path d="M14 2l6 3-8 16-6-3zM10 20l-2 5M15 24a10 10 0 0 0 14-9M18 18h10M4 36h28M8 36v-4h20v4M2 39h32"/></svg></div>
<div class="why-label" style="left:901px;top:1813px">Innovative Research</div>
<div class="why-box" style="left:818px;top:1895px"><svg width="42" height="42" viewBox="0 0 42 42" fill="none" stroke="#555" stroke-width="1.4"><circle cx="21" cy="21" r="19"/><circle cx="21" cy="21" r="15"/><path d="M21 10v11l7 5"/></svg></div>
<div class="why-label" style="left:901px;top:1920px">On Time Solutions</div>
<div class="why-box" style="left:818px;top:2001px"><svg width="40" height="42" viewBox="0 0 40 42" fill="none" stroke="#555" stroke-width="1.4"><path d="M10 18a10 10 0 0 1 20 0"/><rect x="7" y="16" width="5" height="8" rx="1"/><rect x="28" y="16" width="5" height="8" rx="1"/><path d="M30 24c0 4-4 6-8 6M4 41c0-7 7-11 16-11s16 4 16 11M20 30v11"/></svg></div>
<div class="why-label" style="left:901px;top:2026px">Start-up Support</div>

<!-- reviews -->
<h2 class="section-title" style="top:2197px">Customer <span class="accent">Reviews</span></h2>
<div class="section-rule" style="top:2246px"></div>
<div class="abs" style="left:578px;top:2276px;color:#9fc3f2;font-size:90px;line-height:90px;font-weight:700;font-family:Georgia,serif">&ldquo;</div>
<p class="quote">"Lorem ipsum dolor sit amet, consectetuer adipiscing elit, sedmk diam nonummy nibh euismod tincidunt ut laoreet dolore magna aliquam erat volutpat. Suscipit lobortis nisl ut aliquip ex eamo kl commodo consequat."</p>
<p class="abs" style="left:0;width:1200px;top:2417px;text-align:center;font-size:14.5px;font-weight:500;color:#333">-Mr. Ravel Ostrand</p>
<div class="dots blue" style="left:575px;top:2461px"><i class="on"></i><i></i><i></i><i></i></div>
<div class="arrow-box" style="left:141px;top:2372px"><svg width="9" height="16" viewBox="0 0 9 16"><path d="M8 1L1 8l7 7" stroke="#1f7fec" fill="none"/></svg></div>
<div class="arrow-box" style="left:1028px;top:2372px"><svg width="9" height="16" viewBox="0 0 9 16"><path d="M1 1l7 7-7 7" stroke="#1f7fec" fill="none"/></svg></div>

<!-- partners -->
<section class="partners"></section>
<h2 class="section-title" style="top:2602px">Our <span class="accent">Parteners</span></h2>
<div class="section-rule" style="top:2651px"></div>
<div class="arrow-box" style="left:71px;top:2722px"><svg width="9" height="16" viewBox="0 0 9 16"><path d="M8 1L1 8l7 7" stroke="#1f7fec" fill="none"/></svg></div>
<div class="arrow-box" style="left:1099px;top:2722px"><svg width="9" height="16" viewBox="0 0 9 16"><path d="M1 1l7 7-7 7" stroke="#1f7fec" fill="none"/></svg></div>
<div class="tile lift" style="left:141px"><div role="img" aria-label="Partner badge" style="width:110px;height:36px;background:#1f7fec"></div></div>
<div class="tile" style="left:329px"><div role="img" aria-label="Partner badge" style="width:110px;height:36px;background:#8a8d93"></div></div>
<div class="tile" style="left:516px"><div role="img" aria-label="Partner badge" style="width:60px;height:60px;border-radius:50%;background:#8a8d93"></div></div>
<div class="tile" style="left:702px"><div role="img" aria-label="Partner badge" style="width:130px;height:30px;background:#8a8d93"></div></div>
<div class="tile" style="left:889px"><div role="img" aria-label="Partner badge" style="width:120px;height:36px;background:#8a8d93"></div></div>

<!-- footer -->
<footer>
  <div class="footer" role="img" aria-label="Dark tinted laboratory backdrop"></div>
  <div class="f-head" style="left:141px">Quick <span class="accent">Links</span></div>
  <div class="f-line" style="left:141px;top:2934px;width:150px"></div>
  <ul class="f-list" style="left:141px">
    <li>Home</li><li>About Us</li><li>Services</li><li>Resources</li><li>Contact Us</li>
  </ul>
  <div class="f-head" style="left:332px">Contact <span class="accent">Detail</span></div>
  <div class="f-line" style="left:332px;top:2934px;width:210px"></div>
  <div class="f-item" style="left:336px;top:2951px"><svg width="12" height="16" viewBox="0 0 12 16"><path d="M6 15S1 9 1 6a5 5 0 0 1 10 0c0 3-5 9-5 9z" stroke="#fff" fill="none"/><circle cx="6" cy="6" r="1.8" stroke="#fff" fill="none"/></svg><div><b style="font-weight:600">Verantel Dx</b><br><span style="display:block;margin-top:6px">123, Loream Ispam Dollar,<br>Larotee, AB-123 456</span></div></div>
  <div class="f-item" style="left:336px;top:3016px;font-size:13px"><svg width="13" height="13" viewBox="0 0 24 24"><path d="M6.6 10.8a15 15 0 0 0 6.6 6.6l2.2-2.2 4.6 1V20A17 17 0 0 1 3 4h4.5l1 4.6z" stroke="#fff" fill="none" stroke-width="1.6"/></svg>123 456 7890</div>
  <div class="f-item" style="left:336px;top:3049px"><svg width="13" height="10" viewBox="0 0 13 10"><rect x=".5" y=".5" width="12" height="9" stroke="#fff" fill="none"/><path d="M1 1l5.5 4.5L12 1" stroke="#fff" fill="none"/></svg>info@verantel-dx.com</div>

  <div class="f-head" style="left:593px">Newsletter <span class="accent">Signup</span></div>
  <div class="f-line" style="left:593px;top:2934px;width:210px"></div>
  <p class="abs" style="left:595px;top:2947px;width:220px;color:#fff;font-size:11px;line-height:16px">Lorem ipsum dolor sit amet, consectetu adipiscing elit, sedmk diam nonummy.</p>
  <div class="f-input">Email</div>
  <div class="btn" style="left:593px;top:3033px;width:106px;height:31px;border:none;font-size:12px">SUBMIT <svg width="14" height="8" viewBox="0 0 16 8"><path d="M0 4h15M11 1l4 3-4 3" stroke="#fff" fill="none"/></svg></div>

  <div class="brand-name" style="left:921px;top:2943px;width:137px;text-align:center;font-size:21px;color:#fff">Verantel Dx</div>
  <div class="social on" style="left:900px"></div>
  <div class="social" style="left:942px"></div>
  <div class="social" style="left:984px"></div>
  <div class="social" style="left:1026px"></div>
  <div class="copy">Copyright&nbsp; 2019 - Verantel Dx. All Rights Reserved.</div>
</footer>

</body>
</html>
```